Velvet Lantern rebranding my business with a new business card

I have my new logo and now I need a refresher on my business cards. I really want something fun and fresh. I like black background or anything to make the color pop.
Logo
Name: Velvet Lantern
Contact Info as stated below:
Mira Pellow
555-013-4762
Logo
Name: Velvet Lantern
Mira Pellow
555-013-4762
fb.me/VelvetLanternbyMira
Instagram: @VelvetLanternbyMira

Industry/Entity Type

Business

Contact Information for Business Card

double-sided. Logo on one side. Contact info on the other.

Requirements
Must have
• Logo
• Name: Velvet Lantern
• Contact Info as stated below:
• Mira Pellow
• 555-013-4762
• fb.me/VelvetLanternbyMira
• fb.me/VelvetLanternbyMira

```html
<!DOCTYPE html>
<html lang="en">
<head>
<meta charset="utf-8">
<title>Velvet Lantern — Business Card</title>
<link rel="stylesheet" href="https://fonts.googleapis.com/css2?family=Rokkitt:wght@500&family=Roboto+Condensed:wght@300&family=Roboto:wght@400&display=swap">
<style>
  :root {
    --page: #ecebe8;
    --card-white: #ffffff;
    --ink: #2a2a2a;
    --ink-soft: #6b6b6b;
    --band-pink: #f7c3c7;
    --band-rose: #e98aa9;
    --band-violet: #b763cf;
    --teal: #5fcabb;
    --teal-deep: #4fb8a9;
    --logo-pink: #f2a6c4;
    --ring: #f3c9d8;
  }
  * { box-sizing: border-box; margin: 0; padding: 0; }
  html, body { width: 1200px; height: 911px; overflow: hidden; }
  body {
    background: var(--page);
    display: flex;
    flex-direction: column;
    align-items: center;
    justify-content: center;
    gap: 40px;
  }
  .card {
    width: 680px;
    height: 390px;
    border-radius: 22px;
    position: relative;
    overflow: hidden;
    box-shadow: 0 6px 18px rgba(0,0,0,.12);
  }

  /* Front */
  .card-front { background: var(--card-white); }
  .front-logo {
    position: absolute;
    left: 70px; top: 95px;
    width: 170px; height: 170px;
    border-radius: 50%;
    border: 4px solid var(--ring);
    display: flex; align-items: center; justify-content: center;
    gap: 8px;
  }
  .front-logo .logo-dot {
    width: 12px; height: 12px; border-radius: 50%;
    background: var(--logo-pink);
    flex: none;
  }
  .logo-name {
    font-family: 'Rokkitt', serif;
    font-weight: 500;
    color: var(--ink);
    font-size: 20px;
    white-space: nowrap;
  }
  .contact {
    position: absolute;
    left: 290px; top: 118px;
  }
  .contact-name {
    font-family: 'Rokkitt', serif;
    font-weight: 500;
    font-size: 46px;
    color: var(--ink);
    letter-spacing: .5px;
    line-height: 1;
  }
  .contact-line {
    font-family: 'Roboto Condensed', sans-serif;
    font-weight: 300;
    font-size: 22px;
    color: var(--ink-soft);
    margin-top: 12px;
  }
  .contact-line + .contact-line { margin-top: 6px; }
  .front-band {
    position: absolute;
    left: 0; right: 0; bottom: 0;
    height: 46px;
    background: linear-gradient(90deg, var(--band-violet), var(--band-rose) 45%, var(--band-pink));
    display: flex; align-items: center;
    padding-left: 110px;
  }
  .band-web {
    font-family: 'Roboto', sans-serif;
    font-size: 17px;
    letter-spacing: 4px;
    color: var(--ink);
  }

  /* Back */
  .card-back {
    background: linear-gradient(160deg, var(--teal), var(--teal-deep));
  }
  .back-logo {
    position: absolute;
    left: 50%; top: 50%;
    transform: translate(-50%, -50%);
    display: flex; align-items: center; gap: 12px;
  }
  .back-logo .logo-dot {
    width: 18px; height: 18px; border-radius: 50%;
    background: var(--logo-pink);
    flex: none;
  }
  .back-logo .logo-name { font-size: 38px; }
  .back-web {
    position: absolute;
    left: 40px; top: 50%;
    transform: translate(-50%, -50%) rotate(90deg);
    font-family: 'Roboto', sans-serif;
    font-size: 16px;
    letter-spacing: 6px;
    color: var(--ink);
    white-space: nowrap;
  }
</style>
</head>
<body>
  <section class="card card-front">
    <div class="front-logo">
      <span class="logo-dot"></span>
      <span class="logo-name">Velvet Lantern</span>
    </div>
    <div class="contact">
      <h1 class="contact-name">MIRA PELLOW</h1>
      <p class="contact-line">555-013-4762</p>
      <p class="contact-line">fb.me/VelvetLanternbyMira</p>
    </div>
    <div class="front-band">
      <span class="band-web">www.velvetlantern.com</span>
    </div>
  </section>

  <section class="card card-back">
    <p class="back-web">www.velvetlantern.com</p>
    <div class="back-logo">
      <span class="logo-dot"></span>
      <span class="logo-name">Velvet Lantern</span>
    </div>
  </section>
</body>
</html>
```